Infographic

We are looking for a new concept on a particular PPT slide to communicate a before and after scenario.
Updates

Note that this is a B2B (telecom) technology exercise and are looking for two other ideas to decision makers at billion dollar companies in various verticals. 

Target Market(s)

CIOs, CTOs

```html
<!DOCTYPE html>
<html lang="en">
<head>
<meta charset="utf-8">
<title>Super Node Carrier Competition</title>
<link href="https://fonts.googleapis.com/css2?family=Arimo:wght@400;700&display=swap" rel="stylesheet">
<style>
  :root {
    --band-blue: #5a8ebf;
    --heading-blue: #4a86c5;
    --arrow-blue: #5b8ec0;
    --ring-blue: #a9c2dc;
    --node-orange: #f7931e;
    --accent-orange: #f08a1c;
    --text-dark: #333333;
    --white: #ffffff;
    --fiber-grey: #e4e6e9;
    --server-grey: #8a8f96;
    --person-blue: #5a8ebf;
  }
  * { margin: 0; padding: 0; box-sizing: border-box; }
  html, body { width: 1200px; height: 849px; overflow: hidden; background: var(--white); }
  body { font-family: "Arimo", Arial, sans-serif; color: var(--text-dark); }
  .slide { position: relative; width: 1200px; height: 849px; }

  .title-band {
    position: absolute; left: 0; top: 0; width: 1200px; height: 121px;
    background: var(--band-blue);
    display: flex; align-items: center; justify-content: center;
  }
  .title-band h1 {
    color: var(--white); font-weight: 700; font-size: 38px; line-height: 47px;
    text-align: center;
  }

  .section-heading {
    position: absolute; top: 148px; font-size: 25px; font-weight: 700; color: var(--heading-blue);
  }
  .section-heading.old { left: 36px; }
  .section-heading.new { left: 630px; }

  .carrier-art {
    position: absolute; left: 22px; top: 195px; width: 376px; height: 465px;
    border-radius: 50%;
    background: radial-gradient(ellipse at center, #f4f5f6 0%, #e6e8ea 55%, #ffffff 78%);
  }
  .carrier-label {
    position: absolute; left: 110px; top: 515px; width: 200px;
    text-align: center; font-size: 24px; line-height: 30px; color: var(--text-dark);
  }

  .migrate-arrow { position: absolute; left: 412px; top: 363px; width: 228px; height: 130px; }
  .migrate-text {
    position: absolute; left: 418px; top: 392px; width: 172px;
    text-align: center; color: var(--white); font-weight: 700; font-size: 15px; line-height: 20px;
  }

  .network { position: absolute; left: 600px; top: 185px; width: 600px; height: 530px; }
  .node-label { font-size: 13px; fill: var(--white); font-family: "Arimo", Arial, sans-serif; }
  .customer-label {
    position: absolute; left: 780px; top: 457px; width: 240px; text-align: center;
    font-size: 20px; line-height: 24px; color: var(--text-dark);
  }
  .dc-label {
    position: absolute; left: 920px; top: 513px; font-size: 13.5px; line-height: 16px; color: var(--text-dark);
  }

  .caption {
    position: absolute; font-size: 16.5px; line-height: 24px; text-align: center; color: var(--text-dark);
  }
  .caption.old { left: 42px; top: 700px; width: 390px; }
  .caption.new { left: 695px; top: 700px; width: 420px; }
  .footnote {
    position: absolute; left: 640px; top: 782px; width: 540px; text-align: center;
    font-size: 15.5px; line-height: 22px; font-weight: 700; color: var(--accent-orange);
  }
</style>
</head>
<body>
<main class="slide">
  <header class="title-band">
    <h1>The leading, proven approach uses intense carrier<br>competition among “super nodes.”</h1>
  </header>

  <h2 class="section-heading old">Old World: Carriers Dictate Prices</h2>
  <h2 class="section-heading new">New World: Competitive Market Lowers Prices</h2>

  <div class="carrier-art" role="img" aria-label="Illustration of a classic black rotary telephone encircled by swirling white fiber-optic strands"></div>
  <p class="carrier-label">Carrier at<br>the Center</p>

  <svg class="migrate-arrow" viewBox="0 0 228 130" aria-hidden="true">
    <polygon points="0,22 178,22 178,0 228,65 178,130 178,108 0,108" fill="var(--arrow-blue)"/>
  </svg>
  <p class="migrate-text">Migrate safely from bloated MPLS, optical ring and Internet access services</p>

  <svg class="network" viewBox="0 0 600 530">
    <defs>
      <radialGradient id="fiberGlow" cx="50%" cy="50%" r="50%">
        <stop offset="70%" stop-color="#ffffff" stop-opacity="0"/>
        <stop offset="85%" stop-color="var(--fiber-grey)"/>
        <stop offset="100%" stop-color="#ffffff" stop-opacity="0"/>
      </radialGradient>
    </defs>
    <circle cx="296" cy="277" r="290" fill="url(#fiberGlow)" role="img" aria-label="Fiber-optic strands radiating outward from each super node"/>
    <g fill="none" stroke="var(--ring-blue)">
      <circle cx="296" cy="277" r="232" stroke-width="2"/>
      <circle cx="296" cy="277" r="224" stroke-width="2"/>
      <circle cx="296" cy="277" r="216" stroke-width="2"/>
      <circle cx="296" cy="277" r="208" stroke-width="1.5"/>
    </g>

    <ellipse class="customer-figure" cx="300" cy="204" rx="44" ry="64" fill="var(--person-blue)" role="img" aria-label="Silhouette of a customer in business attire"/>

    <path d="M286 347 C 250 350, 246 395, 252 415" fill="none" stroke="var(--node-orange)" stroke-width="3"/>
    <rect x="286" y="330" width="22" height="36" rx="2" fill="#d7dadf" stroke="var(--server-grey)" role="img" aria-label="Customer data center server"/>

    <g class="super-node">
      <circle cx="296" cy="78" r="50" fill="var(--node-orange)"/>
      <rect x="262" y="40" width="68" height="44" rx="3" fill="var(--server-grey)" role="img" aria-label="Server racks"/>
      <text class="node-label" x="296" y="103" text-anchor="middle">super node</text>
    </g>
    <g class="super-node">
      <circle cx="105" cy="218" r="50" fill="var(--node-orange)"/>
      <rect x="71" y="180" width="68" height="44" rx="3" fill="var(--server-grey)" role="img" aria-label="Server racks"/>
      <text class="node-label" x="105" y="243" text-anchor="middle">super node</text>
    </g>
    <g class="super-node">
      <circle cx="485" cy="218" r="50" fill="var(--node-orange)"/>
      <rect x="451" y="180" width="68" height="44" rx="3" fill="var(--server-grey)" role="img" aria-label="Server racks"/>
      <text class="node-label" x="485" y="243" text-anchor="middle">super node</text>
    </g>
    <g class="super-node">
      <circle cx="296" cy="423" r="50" fill="var(--node-orange)"/>
      <rect x="262" y="385" width="68" height="44" rx="3" fill="var(--server-grey)" role="img" aria-label="Server racks"/>
      <text class="node-label" x="296" y="448" text-anchor="middle">super node</text>
    </g>
  </svg>

  <p class="customer-label">Customer at the Center</p>
  <p class="dc-label">Customer’s<br>Data Center</p>

  <p class="caption old">Carrier sells or resells connections to corporate<br>campuses, branches, processing centers, trading<br>partners, application providers</p>
  <p class="caption new">Carrier sells only short tails to third-party data centers<br>that are connected by hundreds of connectivity provid-<br>ers with high performance circuits</p>
  <p class="footnote">Super nodes are transit points within third-party data centers run<br>by leading companies like Northgate, Meridex and Harborline.</p>
</main>
</body>
</html>
```